Landingpage Design X-Mas Invitation

Every year we invite customers to a special X-Mas Apéro. Since we are an IT-Company we handle the registration process by a landingpage. For this we need a design for the event 2016. The content will be the same as 2015 (you will finde the design attached from last year. There will be an additional job for creating the E-Mail.

Target Market(s)

Customers of IT Company, medium Companys in Central Switzerland

Industry/Entity Type

It Company

Number of Pages Required

1 page

Requirements
Must have
• Christmas Style

```html
<!DOCTYPE html>
<html lang="de">
<head>
<meta charset="utf-8">
<title>Brennwald Weihnachtsapéro</title>
<link rel="stylesheet" href="https://fonts.googleapis.com/css2?family=Fira+Sans:wght@300;400;500&display=swap">
<style>
:root{
  --red:#d9493b;
  --red-dark:#b8372a;
  --green-top:#7cbb25;
  --green-bottom:#3f8a12;
  --tree-light:#9fd03a;
  --tree-dark:#4f9418;
  --white:#ffffff;
  --grey-line:#c9c9c9;
  --grey-arrow:#a8a8a8;
}
*{box-sizing:border-box;margin:0;padding:0}
html,body{width:804px;height:1200px;overflow:hidden;background:var(--white)}
body{font-family:"Fira Sans",Arial,sans-serif;color:var(--red);position:relative}
.hero{position:relative;height:455px;overflow:hidden}
.hero-sky{position:absolute;inset:0;width:804px;height:455px}
.corner-ornament{position:absolute;left:0;top:0;width:80px;height:115px;
  background:linear-gradient(135deg,#d3a84a 0%,#5f9a2e 55%,#8cc63f 100%);
  border-bottom-right-radius:40px}
.brand{position:absolute;top:18px;left:0;width:804px;text-align:center;
  font-weight:500;font-size:46px;line-height:56px;color:var(--red);letter-spacing:-.5px}
.tree{position:absolute;left:332px;top:102px;width:128px;height:246px;border-radius:14px;
  background:linear-gradient(var(--tree-light),var(--tree-dark))}
.tilted{position:absolute;font-weight:300;font-size:18px;line-height:24px;
  text-transform:uppercase;color:var(--red);text-align:center;white-space:nowrap}
.tilted.event{left:266px;top:210px;transform:translate(-50%,-50%) rotate(45deg)}
.tilted.date{left:535px;top:215px;transform:translate(-50%,-50%) rotate(-40deg)}
.tilted.venue{left:250px;top:385px;transform:translate(-50%,-50%) rotate(-30deg)}
.intro{width:720px;margin:10px auto 0;text-align:center;font-size:14px;line-height:24px}
.intro p+p{margin-top:9px}
.register{display:block;width:159px;height:38px;margin:27px auto 0;
  background:linear-gradient(var(--red),var(--red-dark));color:var(--white);
  font-size:19px;line-height:38px;text-align:center;text-decoration:none;letter-spacing:.3px}
.contact{position:absolute;top:788px;left:0;width:804px;height:215px;
  background:linear-gradient(var(--green-top),var(--green-bottom));color:var(--white);text-align:center}
.contact h2{font-weight:500;font-size:28px;margin-top:25px;letter-spacing:.5px}
.contact address{font-style:normal;font-size:17px;line-height:24px;margin-top:12px}
.partners{position:absolute;top:1003px;left:0;width:804px;height:122px}
.partner{position:absolute;top:40px;width:138px;height:50px;border:1px solid var(--grey-line)}
.partner::after{content:"";position:absolute;left:44px;top:14px;width:50px;height:20px;background:#e6e6e6}
.arrow{position:absolute;top:57px}
.footer{position:absolute;top:1125px;left:0;width:804px;height:75px;
  background:linear-gradient(#da614d,var(--red-dark));color:var(--white);font-size:14px}
.footer p{position:absolute;top:27px;left:0;width:804px;text-align:center}
.footer .code{position:absolute;right:36px;top:26px;font-size:16px}
</style>
</head>
<body>
<header class="hero">
  <svg class="hero-sky" viewBox="0 0 804 455" aria-hidden="true">
    <defs>
      <linearGradient id="sky" x1="0" y1="0" x2="1" y2="0.4">
        <stop offset="0" stop-color="#8cc63f"/>
        <stop offset=".45" stop-color="#e4f3cf"/>
        <stop offset="1" stop-color="#9ccf55"/>
      </linearGradient>
    </defs>
    <rect width="804" height="200" fill="url(#sky)"/>
    <path fill="#fff" d="M0 125 C40 80 150 70 215 160 C250 95 330 85 400 130 C450 95 540 90 595 155 C640 120 690 115 710 125 C740 95 790 100 804 105 L804 455 L0 455 Z"/>
  </svg>
  <div class="corner-ornament" role="img" aria-label="Tannenzweig mit goldener Schleife"></div>
  <div class="brand">Brennwald</div>
  <div class="tree" role="img" aria-label="Geschmückter Weihnachtsbaum mit Stern und Kugeln"></div>
  <div class="tilted event">Brennwald<br>Weihnachts<br>Apéro</div>
  <div class="tilted date">17. Dezember 2015<br>17 – 20 Uhr</div>
  <div class="tilted venue">Skylounge<br>Talackerweg 12<br>Luzern</div>
</header>

<main>
  <section class="intro">
    <p>Unser traditioneller Brennwald Weihnachtsapéro findet am Donnerstag, dem 17.12.2015, zwischen 17 und 20 Uhr in unserer Skylounge am Talackerweg 12, dem Hauptsitz der Brennwald IT Solutions AG statt. In einem aussergewöhnlichen Ambiente können Sie und Ihre Begleitung köstliche Speisen und Getränke beim Apéro Riche geniessen. Desweiteren bietet sich Ihnen die Gelegenheit, ausgiebige Gespräche mit unserer Geschäftsleitung, unseren Mitarbeitenden sowie weiteren Kunden zu führen. Der Anlass findet in einer lockeren Atmosphäre statt, entsprechend ungezwungen ist der Dresscode.</p>
    <p>Ob Sie den ganzen Abend bleiben oder nur kurz nach dem Weihnachts-Shopping vorbeischauen, ist ganz Ihnen überlassen. Wir freuen uns sehr, wenn Sie uns die Gelegenheit geben, Ihnen mit dieser Einladung für die erfolgreiche Zusammenarbeit herzlichst zu danken.</p>
  </section>
  <a class="register" href="#">ANMELDEN</a>
</main>

<section class="contact">
  <h2>KONTAKT</h2>
  <address>
    Brennwald IT Solutions AG<br>
    Talackerweg 12<br>
    6004 Luzern<br>
    Telefon 041 555 01 20<br>
    E-Mail info@brennwald-it.ch
  </address>
</section>

<section class="partners" aria-label="Partner">
  <svg class="arrow" style="left:30px" width="12" height="20" viewBox="0 0 12 20" aria-hidden="true"><path d="M10 2 L2 10 L10 18" fill="none" stroke="var(--grey-arrow)" stroke-width="2"/></svg>
  <div class="partner" style="left:76px"></div>
  <div class="partner" style="left:246px"></div>
  <div class="partner" style="left:416px"></div>
  <div class="partner" style="left:586px"></div>
  <svg class="arrow" style="left:758px" width="12" height="20" viewBox="0 0 12 20" aria-hidden="true"><path d="M2 2 L10 10 L2 18" fill="none" stroke="var(--grey-arrow)" stroke-width="2"/></svg>
</section>

<footer class="footer">
  <p>© 2016 BRENNWALD IT SOLUTIONS. All Rights Reserved.</p>
  <span class="code">C16</span>
</footer>
</body>
</html>
```